kolvarin.link kolvarin.space kolvarin.press website

The website is named KOLVARIN and it will have 3 domain names. kolvarin.link, press, space.
I'd like it to be viewed on Pads, pcs and phones.

page menu:

kolvarin.link(start page): presentation of company. (creative, design, app, new product innovation.)
Here we'll need sosial media icons: plimber, vendoloop, mirtavel, trelvanet. (light but some 'fruity' colors)

kolvarin.press: blog. It will be a 75% picture blog > rest will be text. I need to be able to resize pictures and shape columns to picture size. (light but some 'fruity' colors)

kolvarin.space : the fun part of this web design, however, on entering the page I'd like a non-disclosure agreement where viewer simply click "yes, I agree" after filling out contact info. (check attached document)
We will have space here for uploading PDF files viewers can download. There is also a blog space here to tell in brief about the PDF file. (maybe a space/sci-fi theme her e.g spacechimp, Laika the space dog?)

I will attach the logo here I want you to use > and develop for the .space .press webpage. The logo i uploaded is for the .link page.

Target Market(s)

venture capitalists

Number of Pages Required

3 page

Requirements
Must have
• a few 'fruity colors' but mostly white and grey

```html
<!DOCTYPE html>
<html lang="en">
<head>
<meta charset="utf-8">
<title>KOLVARIN — Creative design, app creation, new product innovation</title>
<link href="https://fonts.googleapis.com/css2?family=Silkscreen:wght@400;700&family=Open+Sans:wght@400;600&display=swap" rel="stylesheet">
<style>
  :root {
    --red: #e2412b;
    --ink: #1d1d1d;
    --body: #4a4a4a;
    --hero-light: #fafafa;
    --hero-grey: #dcdcdc;
    --dark: #111111;
    --footer: #3b3b3b;
    --white: #ffffff;
    --line: #dedede;
    --blue: #2c8ed8;
    --yellow: #f1c21b;
    --tomato: #e23a2c;
    --berry: #d8432f;
    --display: "Silkscreen", monospace;
    --text: "Open Sans", Arial, sans-serif;
  }
  * { box-sizing: border-box; margin: 0; padding: 0; }
  a { text-decoration: none; color: inherit; }
  html, body { width: 790px; height: 1200px; overflow: hidden; background: var(--white); }
  body { font-family: var(--text); color: var(--body); }
  .canvas { position: relative; width: 790px; height: 1200px; overflow: hidden; }

  /* Hero */
  .hero {
    position: absolute; left: 0; top: 0; width: 790px; height: 442px;
    background: linear-gradient(135deg, var(--hero-light) 0%, #eeeeee 45%, var(--hero-grey) 75%, #f1f1f1 100%);
  }
  .brand { position: absolute; left: 64px; top: 48px; display: flex; align-items: center; gap: 8px; }
  .brand-mark { width: 14px; height: 14px; background: var(--red); }
  .brand-name { font-family: var(--display); font-weight: 700; font-size: 22px; color: var(--ink); }
  .main-nav { position: absolute; top: 56px; left: 297px; display: flex; gap: 18px; align-items: center; }
  .main-nav a { font-family: var(--display); font-size: 8px; color: var(--ink); }
  .main-nav a.is-active { color: var(--red); }
  .intro { position: absolute; left: 160px; top: 178px; width: 292px; }
  .intro-title { font-family: var(--display); font-weight: 700; font-size: 19px; color: var(--ink); }
  .intro-services { margin-top: 10px; font-size: 7.5px; color: var(--red); text-transform: uppercase; }
  .intro-text { margin-top: 11px; font-size: 7.6px; line-height: 14.7px; color: var(--body); }
  .store-links { position: absolute; left: 160px; top: 311px; display: flex; gap: 9px; }
  .store-badge {
    width: 91px; height: 26px; background: #000; border: 1px solid #777; border-radius: 3px;
    display: flex; align-items: center; gap: 5px; padding-left: 6px; color: var(--white);
  }
  .store-badge svg { flex: none; }
  .store-badge small { display: block; font-size: 5px; line-height: 6px; }
  .store-badge strong { display: block; font-size: 10px; font-weight: 400; line-height: 11px; }
  .slider-dots { position: absolute; display: flex; gap: 8px; }
  .slider-dots span { width: 32px; height: 1px; background: var(--ink); }
  .slider-dots span.is-current { background: var(--red); }
  .hero .slider-dots { left: 161px; top: 355px; }
  .hero-visual {
    position: absolute; left: 520px; top: 134px; width: 240px; height: 308px;
    border-radius: 14px 14px 0 0;
    background: linear-gradient(180deg, #d9d9d9 0%, #cfc4bc 55%, #d8b9a4 100%);
  }

  /* Features */
  .features {
    position: absolute; left: 0; top: 442px; width: 790px; height: 350px;
    background: radial-gradient(ellipse at 50% 45%, #3a1f14 0%, #1b100b 45%, var(--dark) 100%);
    text-align: center;
  }
  .section-title { font-family: var(--display); font-weight: 700; font-size: 19px; }
  .features .section-title { position: absolute; top: 24px; width: 100%; color: var(--white); }
  .feature-devices { position: absolute; left: 203px; top: 76px; display: flex; gap: 56px; }
  .feature-device {
    width: 92px; height: 176px; border-radius: 12px;
    background: linear-gradient(180deg, #d8d8d8 0 12%, #1f5d68 12% 86%, #d8d8d8 86%);
    opacity: 0.75;
  }
  .feature-device.is-current { opacity: 1; background: linear-gradient(180deg, #f4f4f4 0 12%, #1f6a76 12% 86%, #f4f4f4 86%); }
  .feature-name { position: absolute; top: 265px; width: 100%; font-family: var(--display); font-weight: 700; font-size: 10px; color: var(--white); }
  .feature-text { position: absolute; top: 282px; left: 225px; width: 340px; font-size: 7.8px; line-height: 14.5px; color: var(--white); }
  .features .slider-dots { left: 340px; top: 328px; }
  .features .slider-dots span { background: #3d3d3d; }
  .features .slider-dots span.is-current { background: var(--red); }

  /* Testimonials */
  .testimonials { position: absolute; left: 0; top: 792px; width: 790px; height: 295px; background: var(--white); text-align: center; }
  .testimonials .section-title { position: absolute; top: 40px; width: 100%; color: var(--ink); }
  .testimonials-intro { position: absolute; top: 79px; left: 145px; width: 500px; font-size: 7.8px; line-height: 14.5px; color: var(--body); }
  .quote-card { position: absolute; left: 122px; top: 118px; width: 546px; height: 82px; border: 1px solid var(--line); background: var(--white); }
  .quote-text { margin: 16px 16px 0; font-size: 7.8px; line-height: 14.5px; color: var(--body); }
  .quote-author { margin-top: 8px; font-size: 10px; color: var(--red); }
  .quote-pointer { position: absolute; left: 268px; bottom: -6px; width: 10px; height: 10px; background: var(--white); border-right: 1px solid var(--line); border-bottom: 1px solid var(--line); transform: rotate(45deg); }
  .client-avatar { position: absolute; left: 364px; top: 216px; width: 62px; height: 62px; border-radius: 50%; background: radial-gradient(circle at 50% 45%, #b8a496 0%, #7d7370 60%, #5d5a5a 100%); border: 2px solid #e4e4e4; }

  /* Footer */
  .site-footer { position: absolute; left: 0; top: 1087px; width: 790px; height: 113px; background: var(--footer); text-align: center; color: var(--white); }
  .social-links { position: absolute; top: 20px; width: 100%; display: flex; justify-content: center; gap: 12px; }
  .social-link { display: flex; align-items: center; gap: 4px; font-size: 7.5px; color: var(--white); }
  .social-link i { width: 9px; height: 9px; display: block; }
  .footer-nav { position: absolute; top: 54px; width: 100%; display: flex; justify-content: center; gap: 12px; }
  .footer-nav a { font-size: 8px; color: var(--white); }
  .copyright { position: absolute; top: 73px; width: 100%; font-size: 8.6px; }
</style>
</head>
<body>
<div class="canvas">

  <header class="hero">
    <a class="brand" href="#">
      <span class="brand-mark"></span>
      <span class="brand-name">KOLVARIN</span>
    </a>
    <nav class="main-nav">
      <a class="is-active" href="#">Home</a>
      <a href="#">Abouts</a>
      <a href="#">Creative design</a>
      <a href="#">App creation</a>
      <a href="#">Download</a>
      <a href="#">Contact</a>
      <svg width="9" height="9" viewBox="0 0 10 10" aria-label="Search"><circle cx="4" cy="4" r="3" fill="none" stroke="#1d1d1d" stroke-width="1.4"/><line x1="6.2" y1="6.2" x2="9.2" y2="9.2" stroke="#1d1d1d" stroke-width="1.4"/></svg>
    </nav>

    <section class="intro">
      <h1 class="intro-title">WE PROVIDE</h1>
      <p class="intro-services">Creative design, app creation, new product innovation etc.</p>
      <p class="intro-text">Lorem Ipsum is simply dummy text of the printing and typesetting industry. Lorem Ipsum has been the industry's standard dummy text ever since the 1500s, when an unknown printer took a galley of type and scrambled it to make a type specimen book.</p>
    </section>

    <div class="store-links">
      <a class="store-badge" href="#">
        <svg width="12" height="14" viewBox="0 0 12 14"><polygon points="1,1 11,7 1,13" fill="#ffffff"/></svg>
        <span><small>Get it on</small><strong>Tindra Play</strong></span>
      </a>
      <a class="store-badge" href="#">
        <svg width="12" height="14" viewBox="0 0 12 14"><rect x="1" y="2" width="10" height="10" rx="2" fill="#ffffff"/></svg>
        <span><small>Available on the</small><strong>Orvel Store</strong></span>
      </a>
    </div>

    <div class="slider-dots"><span></span><span></span><span class="is-current"></span></div>

    <div class="hero-visual" role="img" aria-label="Photo of a hand holding a phone showing the KOLVARIN sign-in screen"></div>
  </header>

  <section class="features">
    <h2 class="section-title">OUR FEATURE</h2>
    <div class="feature-devices">
      <div class="feature-device" role="img" aria-label="Phone showing a speed tracking app screen"></div>
      <div class="feature-device is-current" role="img" aria-label="Phone showing a speed tracking app screen"></div>
      <div class="feature-device" role="img" aria-label="Phone showing a speed tracking app screen"></div>
    </div>
    <h3 class="feature-name">CREATIVE DESIGN</h3>
    <p class="feature-text">Lorem Ipsum is simply dummy text of the printing and typesetting industry. Lorem Ipsum has been the industry's standard dummy text ever since the 1500s,</p>
    <div class="slider-dots"><span></span><span></span><span class="is-current"></span></div>
  </section>

  <section class="testimonials">
    <h2 class="section-title">WHAT CLIENTS SAY</h2>
    <p class="testimonials-intro">Duis bibendum diam non erat facilaisis tincidunt. Fusce leo neque, lacinia at tempor vitae, porta at arcu. Vestibulum varius non dui at pulvinar. Ut egestas orci in quam sollicitudin aliquet.</p>
    <blockquote class="quote-card">
      <p class="quote-text">Vivamus enim nisi, dictum vel cursus a, pulvinar a neque. Aenean interdum, tellus ut congue rutrum, urna leo bibendum erat, vel ullamcorper eros tellus vitae libero. Nulla tellus vitae nibh , a viverra est malesuada. Nam malesuada quis tellus eu laoreet.</p>
      <p class="quote-author">Client Name</p>
      <span class="quote-pointer"></span>
    </blockquote>
    <div class="client-avatar" role="img" aria-label="Portrait photo of the client"></div>
  </section>

  <footer class="site-footer">
    <div class="social-links">
      <a class="social-link" href="#"><i style="background: var(--blue)"></i>mirtavel</a>
      <a class="social-link" href="#"><i style="background: var(--yellow)"></i>plimber</a>
      <a class="social-link" href="#"><i style="background: var(--tomato)"></i>vendoloop</a>
      <a class="social-link" href="#"><i style="background: var(--berry)"></i>trelvanet</a>
    </div>
    <nav class="footer-nav">
      <a href="#">Creative design</a>
      <a href="#">App creation</a>
      <a href="#">Download</a>
      <a href="#">Contact</a>
    </nav>
    <p class="copyright">Copyright @ 2015 - 2016. KOLVARIN. All Rights Reserved.</p>
  </footer>

</div>
</body>
</html>
```